Personalized Technology Company Needs a Business Card

I need a double-sided business card. Both sides will have the logo, and the contact information. One side will be black, with the white / gray logo, and the other will be white, with the black / gray logo. The black side will have the text "Custom Gaming PC's" and will have a water-cooled gaming PC image. The white side will have the text "Custom Business Computers & Consulting", and will have a business / enterprise PC image. Feel free to add a conservative image in the background, while the color remains unchanged. I'm uploading the base logo (transparent), so you can modify the colors, both the finished colored logos and an idea of ​​the business card (with the current information, just missing the website, which is www.velomindsystems.com, please add it.) Thank you so much for your effort, I'll be specting your cool designs. Good Luck!

Target Market(s)

Gamers & Entrepreneurs / Business Owners / Chief Technology Officers

Industry/Entity Type

Technology Equipment

Contact Information for Business Card

I need a double-sided business card. Both sides will have the logo, and the contact information. One side will be black, with the white/gray logo, and the other one will be white, with the black/gray logo. The black side will have the text "Custom Gaming PC's" and will have a water-cooled gaming PC image. The white side will have the text "Custom Business Computers & Consulting", and will have a business/enterprise PC image. Feel free to add a conservative image in the background, whilst the color remains unchanged.

I'm uploading the base logo (transparent), so you can modify the colors, both the finished colored logos and an idea of the business card (with the actual information, just missing the website, which is www.velomindsystems.com, please add it.)

Thank you so much for your effort, I'll be specting your cool designs. Good Luck!

Font styles to use
Serif

Colors
000000
757575
ffffff

Requirements
Must have
• Please See Description
Nice to have
• Please See Description
Should not have
• Please See Description

```html
<!DOCTYPE html>
<html lang="en">
<head>
<meta charset="utf-8">
<title>Velomind Systems – Business Card</title>
<link rel="stylesheet" href="https://fonts.googleapis.com/css2?family=Tinos:wght@400;700&display=swap">
<style>
  :root {
    --ink: #000000;
    --grey: #757575;
    --paper: #ffffff;
    --stage: #e9e9ec;
    --photo-deep: #0a1a5c;
    --photo-mid: #1d4fd1;
    --photo-glow: #5fd0f5;
    --emblem-dark: #1c1c1c;
    --emblem-light: #ececec;
  }
  * { margin: 0; padding: 0; box-sizing: border-box; }
  html, body { width: 1200px; height: 800px; overflow: hidden; }
  body {
    background: var(--stage);
    font-family: "Tinos", "Times New Roman", serif;
    display: flex; align-items: center; justify-content: center; gap: 40px;
  }
  .card {
    position: relative; width: 560px; height: 320px; overflow: hidden;
    box-shadow: 0 10px 30px rgba(0,0,0,.25);
  }
  .card--dark { background: var(--ink); color: var(--paper); }
  .card--light { background: var(--paper); color: var(--ink); }

  .card__photo {
    position: absolute; inset: 0;
    background:
      radial-gradient(circle at 70% 35%, var(--photo-glow) 0%, transparent 45%),
      linear-gradient(135deg, var(--photo-mid), var(--photo-deep));
  }
  .card--dark .card__photo {
    clip-path: polygon(52% 0, 100% 0, 100% 80%, 88% 84%, 78% 80%, 68% 86%, 60% 82%, 56% 74%, 50% 70%, 53% 60%, 47% 52%, 51% 42%, 45% 34%, 50% 24%, 46% 14%, 51% 6%);
  }
  .card--light .card__photo {
    clip-path: polygon(62% 0, 100% 0, 100% 100%, 78% 100%, 74% 92%, 70% 84%, 66% 76%, 70% 68%, 64% 60%, 67% 50%, 60% 42%, 64% 32%, 58% 24%, 62% 14%, 57% 6%);
  }

  .card__emblem {
    position: absolute; border-radius: 48% 52% 40% 60% / 55% 45% 55% 45%;
  }
  .card--dark .card__emblem { left: 150px; top: 120px; width: 220px; height: 200px; background: radial-gradient(circle, var(--emblem-dark), transparent 72%); }
  .card--light .card__emblem { left: 130px; top: 140px; width: 260px; height: 220px; background: radial-gradient(circle, var(--emblem-light), transparent 72%); }

  .brand { position: absolute; display: flex; align-items: center; gap: 12px; }
  .brand__mark { width: 44px; height: 44px; border-radius: 50%; background: var(--grey); flex: none; }
  .brand__name { font-size: 38px; font-weight: 700; letter-spacing: 3px; line-height: 1; }
  .brand__sub { font-size: 12px; letter-spacing: 6px; color: var(--grey); margin-top: 4px; }
  .card--dark .brand { left: 34px; top: 52px; }
  .card--light .brand { left: 46px; top: 110px; }

  .person { position: absolute; left: 34px; top: 138px; }
  .person__name { font-size: 19px; font-weight: 700; }
  .person__role { font-size: 13px; color: #cfcfcf; }

  .contact { position: absolute; left: 34px; list-style: none; font-size: 13px; }
  .contact li { display: flex; align-items: center; gap: 8px; line-height: 20px; }
  .contact svg { width: 12px; height: 12px; fill: var(--paper); flex: none; }
  .contact--phones { top: 188px; }
  .contact--web { top: 244px; }
  .divider { position: absolute; left: 34px; top: 236px; width: 230px; border-top: 1px dotted var(--grey); }

  .tagline {
    position: absolute; display: flex; align-items: center; justify-content: center;
    text-transform: uppercase; text-align: center; letter-spacing: 1px;
  }
  .card--dark .tagline {
    left: 312px; top: 216px; width: 222px; height: 34px;
    background: var(--ink); color: var(--paper); font-size: 14px; border-radius: 3px;
  }
  .card--light .tagline {
    left: 354px; top: 196px; width: 186px; height: 56px;
    background: var(--paper); color: var(--ink); font-size: 13px; line-height: 1.2;
    border: 3px solid #b8aea6;
  }

  .social { position: absolute; left: 46px; top: 272px; display: flex; align-items: center; gap: 8px; font-size: 13px; }
  .social__dot { width: 16px; height: 16px; border-radius: 50%; background: var(--ink); }
  .social__url { margin-left: 6px; }
</style>
</head>
<body>

  <section class="card card--dark" aria-label="Card front, dark side">
    <div class="card__photo" role="img" aria-label="Water-cooled gaming PC interior with blue lighting"></div>
    <div class="card__emblem" role="img" aria-label="Faint brand emblem decoration"></div>

    <div class="brand">
      <span class="brand__mark"></span>
      <div>
        <div class="brand__name">VELOMIND</div>
        <div class="brand__sub">SYSTEMS</div>
      </div>
    </div>

    <div class="person">
      <div class="person__name">Marco Ruiz Tellan</div>
      <div class="person__role">(CEO &amp; Co-Founder)</div>
    </div>

    <ul class="contact contact--phones">
      <li><svg viewBox="0 0 24 24"><path d="M6.6 10.8a15 15 0 0 0 6.6 6.6l2.2-2.2c.3-.3.7-.4 1-.2 1.1.4 2.3.6 3.6.6.6 0 1 .4 1 1V20c0 .6-.4 1-1 1A17 17 0 0 1 3 4c0-.6.4-1 1-1h3.5c.6 0 1 .4 1 1 0 1.3.2 2.5.6 3.6.1.3 0 .7-.2 1z"/></svg>+52 5100 - 2233</li>
      <li><svg viewBox="0 0 24 24"><path d="M6.6 10.8a15 15 0 0 0 6.6 6.6l2.2-2.2c.3-.3.7-.4 1-.2 1.1.4 2.3.6 3.6.6.6 0 1 .4 1 1V20c0 .6-.4 1-1 1A17 17 0 0 1 3 4c0-.6.4-1 1-1h3.5c.6 0 1 .4 1 1 0 1.3.2 2.5.6 3.6.1.3 0 .7-.2 1z"/></svg>+52 55 - 4810 - 3361</li>
    </ul>
    <div class="divider"></div>
    <ul class="contact contact--web">
      <li><svg viewBox="0 0 24 24"><path d="M2 5h20v14H2zM4 7v.5l8 5 8-5V7z"/></svg>contact@velomindsystems.com</li>
      <li><svg viewBox="0 0 24 24"><path d="M4 12h14l-5-5 1.4-1.4L22 13l-7.6 7.4L13 19l5-5H4z"/></svg>www.velomindsystems.com</li>
    </ul>

    <div class="tagline">Custom Gaming PC's</div>
  </section>

  <section class="card card--light" aria-label="Card back, light side">
    <div class="card__photo" role="img" aria-label="Business enterprise computer hardware with blue lighting"></div>
    <div class="card__emblem" role="img" aria-label="Faint brand emblem decoration"></div>

    <div class="brand">
      <span class="brand__mark"></span>
      <div>
        <div class="brand__name">VELOMIND</div>
        <div class="brand__sub">SYSTEMS</div>
      </div>
    </div>

    <div class="tagline">Custom Business<br>Computers &amp; Consulting</div>

    <div class="social">
      <span class="social__dot"></span>
      <span class="social__dot"></span>
      <span class="social__dot"></span>
      <span class="social__url">www.velomindsystems.com</span>
    </div>
  </section>

</body>
</html>
```